SafePlay Index ratings for Apps and Games

I need a web site designing that is aimed at parents and will show an "SafePlay Index" rating for apps and games. I have attached a document with an overview of what the SafePlay Index is. The website needs to be easy for parents to navigate and find what they want quickly and easily. I should also be able to update the website myself easily with "reviews" of the attack vectors for apps and games.

Target Market(s)

Parents

Coding

Coded - Design and coding required

Number of Pages Required

2 page

Requirements
Must have
• Clear and concise ratings for apps and games

```html
<!DOCTYPE html>
<html lang="en">
<head>
<meta charset="utf-8">
<title>SafePlay Index – App &amp; Game Safety Ratings for Parents</title>
<link rel="stylesheet" href="https://fonts.googleapis.com/css2?family=Rubik:wght@500;700&family=Roboto:wght@400;500;700&display=swap">
<style>
:root{
  --blue:#1e88e5;
  --ink:#1f1f1f;
  --text:#7a7a7a;
  --white:#ffffff;
  --footer:#333333;
  --footer-text:#e6e6e6;
  --card-shadow:0 2px 14px rgba(0,0,0,.12);
}
*{margin:0;padding:0;box-sizing:border-box}
html,body{width:1200px;height:4203px;overflow:hidden;background:var(--white)}
body{position:relative;font-family:"Roboto",Arial,sans-serif;color:var(--ink)}

/* header */
.site-header{position:absolute;left:0;top:0;width:1200px;height:78px;background:var(--white)}
.brand{position:absolute;left:111px;top:26px;font:700 21px/26px "Rubik",sans-serif;color:#333;letter-spacing:.3px;white-space:nowrap}
.main-nav a{position:absolute;top:31px;font:500 13px/16px "Roboto",sans-serif;color:#222;text-decoration:none;letter-spacing:.3px;white-space:nowrap}
.main-nav a.active{color:var(--blue)}
.btn{display:inline-flex;align-items:center;justify-content:center;gap:9px;background:var(--blue);color:var(--white);border-radius:24px;font:700 13px/1 "Roboto",sans-serif;letter-spacing:.4px;text-decoration:none;white-space:nowrap}
.signup{position:absolute;left:995px;top:20px;width:113px;height:39px}

/* hero */
.hero{position:absolute;left:0;top:78px;width:1200px;height:551px;background:linear-gradient(100deg,#d9d1c6 0%,#b9a996 35%,#8f9c9a 62%,#5d6f78 100%)}
.hero-title{position:absolute;left:109px;top:254px;font:700 46px/52px "Rubik",sans-serif;color:var(--white);white-space:nowrap}
.hero-sub{position:absolute;left:109px;top:325px;width:410px;font:500 16.5px/25px "Roboto",sans-serif;color:var(--white)}
.hero-btn{position:absolute;left:109px;top:396px;width:162px;height:47px}
.slider-dots{position:absolute;left:1139px;top:302px;width:8px}
.slider-dots span{display:block;width:8px;height:8px;border-radius:50%;background:var(--white);margin-bottom:15px}
.slider-dots span.open{background:transparent;border:1.5px solid var(--white)}

/* feature rows */
.feature-photo{position:absolute;width:499px;height:422px}
.feature-card{position:absolute;width:477px;height:336px;background:var(--white);box-shadow:var(--card-shadow);padding:35px 38px 0 38px}
.feature-card h2{font:700 29px/36px "Rubik",sans-serif;color:var(--ink);letter-spacing:.3px;white-space:nowrap}
.feature-card .rule{width:36px;height:2px;background:var(--blue);margin:14px 0 16px}
.feature-card p{font:400 13.8px/27.4px "Roboto",sans-serif;color:var(--text);width:410px;height:137px;overflow:hidden}
.feature-card .btn{width:162px;height:48px;margin-top:14px}

/* testimonials */
.testimonials{position:absolute;left:0;top:3360px;width:1200px;height:464px;background:linear-gradient(180deg,#2a8fe6,#1e86e0)}
.testimonials-title{position:absolute;left:0;top:3419px;width:1200px;text-align:center;font:700 34px/40px "Rubik",sans-serif;color:var(--white);letter-spacing:.5px}
.quote{position:absolute;top:3542px;width:305px;color:var(--white)}
.quote p{margin-top:16px;font:400 14px/28.5px "Roboto",sans-serif;opacity:.95}
.stars{margin-top:6px;font-size:14px;line-height:18px;letter-spacing:2px}
.quote cite{display:block;margin-top:14px;font:400 14px/18px "Roboto",sans-serif;font-style:normal;white-space:nowrap}

/* footer */
.site-footer{position:absolute;left:0;top:3824px;width:1200px;height:379px;background:var(--footer)}
.foot-col{position:absolute;top:3868px;color:var(--footer-text)}
.foot-col h3{font:500 14px/18px "Roboto",sans-serif;color:var(--white);white-space:nowrap}
.foot-col h3::after{content:"";display:block;width:50px;height:2px;background:var(--white);margin-top:8px}
.foot-col ul{list-style:none;margin-top:23px}
.foot-col li{font:400 14px/16px "Roboto",sans-serif;margin-bottom:16.5px;white-space:nowrap;color:var(--footer-text)}
.foot-col li::before{content:"»";margin-right:14px}
.address{display:flex;gap:15px;margin-top:26px;font:400 14px/22px "Roboto",sans-serif}
.contact-bar{position:absolute;left:163px;top:4041px;width:874px;height:59px;background:var(--blue);color:var(--white)}
.contact-item{position:absolute;top:0;height:59px;display:flex;align-items:center;gap:23px;font:400 16.5px/1 "Roboto",sans-serif;white-space:nowrap}
.contact-item .icon{width:40px;height:40px;border:1.5px solid var(--white);border-radius:50%;display:flex;align-items:center;justify-content:center;flex:none}
.divider{position:absolute;top:10px;width:1px;height:39px;background:rgba(255,255,255,.55)}
.copyright{position:absolute;left:0;top:4145px;width:1200px;text-align:center;font:400 14px/18px "Roboto",sans-serif;color:var(--footer-text)}
</style>
</head>
<body>

<header class="site-header">
  <div class="brand">SAFEPLAY INDEX</div>
  <nav class="main-nav">
    <a class="active" style="left:370px" href="#">HOME</a>
    <a style="left:435px" href="#">ABOUT US</a>
    <a style="left:530px" href="#">LIVE STREAMING</a>
    <a style="left:675px" href="#">LOCATION SERVICES</a>
    <a style="left:845px" href="#">CONTACT US</a>
  </nav>
  <a class="btn signup" href="#">SIGN UP
    <svg width="11" height="12" viewBox="0 0 11 12"><rect x="1" y="5" width="9" height="7" rx="1" fill="#fff"/><path d="M3 5V3.5a2.5 2.5 0 0 1 5 0V5" fill="none" stroke="#fff" stroke-width="1.6"/></svg>
  </a>
</header>

<section class="hero" role="img" aria-label="Photo of a smiling girl using a laptop at home"></section>
<h1 class="hero-title">SAFEPLAY INDEX</h1>
<p class="hero-sub">Clear safety ratings for every app and game, so parents can choose quickly</p>
<a class="btn hero-btn" href="#">GET STARTED
  <svg width="14" height="14" viewBox="0 0 14 14"><circle cx="7" cy="7" r="7" fill="#fff"/><path d="M5.5 4l3 3-3 3" fill="none" stroke="#1e88e5" stroke-width="1.8"/></svg>
</a>
<div class="slider-dots"><span></span><span></span><span class="open"></span><span></span><span></span></div>

<div class="feature-photo" style="left:134px;top:738px;background:linear-gradient(135deg,#e7ddd2,#b99a80 55%,#7e8a86)" role="img" aria-label="Photo of a mother helping her daughter with homework"></div>
<article class="feature-card" style="left:588px;top:782px">
  <h2>LOGIN</h2><div class="rule"></div>
  <p>Every app and game gets a Login rating from one to five. We check what details sign-up asks for, whether a child can make an account alone, if parents can lock the settings and how easily a stranger could reach a profile. A low score means low risk for your child.</p>
  <a class="btn" href="#">LEARN MORE <svg width="14" height="14" viewBox="0 0 14 14"><circle cx="7" cy="7" r="7" fill="#fff"/><path d="M5.5 4l3 3-3 3" fill="none" stroke="#1e88e5" stroke-width="1.8"/></svg></a>
</article>

<div class="feature-photo" style="left:564px;top:1262px;background:linear-gradient(135deg,#f1f1f1,#c7b3a3 50%,#8f4a46)" role="img" aria-label="Photo of a father and son celebrating at a desk"></div>
<article class="feature-card" style="left:132px;top:1306px">
  <h2>CHAT/MESSAGING</h2><div class="rule"></div>
  <p>Our Chat rating shows who can message your child inside each app or game. We look at open chat with strangers, friend requests, voice rooms, filters for bad words and whether parents can switch chat off. Each review ends with a clear score from one to five.</p>
  <a class="btn" href="#">LEARN MORE <svg width="14" height="14" viewBox="0 0 14 14"><circle cx="7" cy="7" r="7" fill="#fff"/><path d="M5.5 4l3 3-3 3" fill="none" stroke="#1e88e5" stroke-width="1.8"/></svg></a>
</article>

<div class="feature-photo" style="left:134px;top:1786px;background:linear-gradient(135deg,#cfc6bd,#8c7464 50%,#4b3c3a)" role="img" aria-label="Photo of a family gathered around a laptop"></div>
<article class="feature-card" style="left:588px;top:1830px">
  <h2>MICROPHONE ACCESS</h2><div class="rule"></div>
  <p>The Microphone rating tells you if an app or game can listen or record. We check when it asks for the mic and camera, whether audio is shared with other players, and if recordings are stored. Apps that never need access score best on our scale.</p>
  <a class="btn" href="#">LEARN MORE <svg width="14" height="14" viewBox="0 0 14 14"><circle cx="7" cy="7" r="7" fill="#fff"/><path d="M5.5 4l3 3-3 3" fill="none" stroke="#1e88e5" stroke-width="1.8"/></svg></a>
</article>

<div class="feature-photo" style="left:564px;top:2310px;background:linear-gradient(135deg,#e4e0da,#a79c8e 50%,#40506a)" role="img" aria-label="Photo of a mother and teenage daughter using a laptop"></div>
<article class="feature-card" style="left:132px;top:2354px">
  <h2>LOCATION SERVICES</h2><div class="rule"></div>
  <p>Our Location rating shows whether an app or game can see where your child is. We check if it asks for GPS, shows nearby players, shares places on a map or keeps a history of visits. Every review lists the settings to change and gives a score from one to five.</p>
  <a class="btn" href="#">LEARN MORE <svg width="14" height="14" viewBox="0 0 14 14"><circle cx="7" cy="7" r="7" fill="#fff"/><path d="M5.5 4l3 3-3 3" fill="none" stroke="#1e88e5" stroke-width="1.8"/></svg></a>
</article>

<div class="feature-photo" style="left:134px;top:2834px;background:linear-gradient(135deg,#ddd6cc,#9aa6b4 50%,#2f3844)" role="img" aria-label="Photo of a mother and daughter watching a laptop in the kitchen"></div>
<article class="feature-card" style="left:588px;top:2878px">
  <h2>LIVE STREAMING</h2><div class="rule"></div>
  <p>The Streaming rating tells you if your child can broadcast live or watch streams from strangers. We check live video, gifts and tips, public comments and how fast reports are handled. Each app and game gets a simple score so you can decide in seconds.</p>
  <a class="btn" href="#">LEARN MORE <svg width="14" height="14" viewBox="0 0 14 14"><circle cx="7" cy="7" r="7" fill="#fff"/><path d="M5.5 4l3 3-3 3" fill="none" stroke="#1e88e5" stroke-width="1.8"/></svg></a>
</article>

<section class="testimonials" role="img" aria-label="Faint blue-tinted photo of a child with headphones behind the testimonials"></section>
<h2 class="testimonials-title">WHAT OUR CLIENTS SAYS</h2>

<blockquote class="quote" style="left:103px">
  <svg width="32" height="26" viewBox="0 0 32 26" fill="#fff"><path d="M0 26V14C0 6 4 1 12 0v5c-4 1-6 4-6 8h6v13zM18 26V14c0-8 4-13 12-14v5c-4 1-6 4-6 8h6v13z"/></svg>
  <p>The ratings are clear and quick to read. I checked every game on my son's tablet in one evening and changed the chat settings</p>
  <div class="stars">★★★★★</div>
  <cite>Dana M. Collins , Businessman</cite>
</blockquote>
<blockquote class="quote" style="left:450px">
  <svg width="32" height="26" viewBox="0 0 32 26" fill="#fff"><path d="M0 26V14C0 6 4 1 12 0v5c-4 1-6 4-6 8h6v13zM18 26V14c0-8 4-13 12-14v5c-4 1-6 4-6 8h6v13z"/></svg>
  <p>I had no idea one app shared location with other players. The score showed it straight away and told me how to turn it off</p>
  <div class="stars">★★★★★</div>
  <cite>Dana M. Collins , Businessman</cite>
</blockquote>
<blockquote class="quote" style="left:797px">
  <svg width="32" height="26" viewBox="0 0 32 26" fill="#fff"><path d="M0 26V14C0 6 4 1 12 0v5c-4 1-6 4-6 8h6v13zM18 26V14c0-8 4-13 12-14v5c-4 1-6 4-6 8h6v13z"/></svg>
  <p>Before any new download we look up its rating together. It has made talking about online safety easy for the whole family</p>
  <div class="stars">★★★★★</div>
  <cite>Dana M. Collins , Businessman</cite>
</blockquote>

<footer class="site-footer"></footer>
<div class="foot-col" style="left:114px"><h3>QUICK LINKS</h3><ul><li>Home</li><li>About Us</li><li>Chat / Messaging</li></ul></div>
<div class="foot-col" style="left:323px"><h3>OTHER LINKS</h3><ul><li>Terms Of Use</li><li>Privacy Policy</li><li>FAQ</li></ul></div>
<div class="foot-col" style="left:523px"><h3>HELPFUL LINKS</h3><ul><li>Camera / Microphone Access</li><li>Location Services</li><li>Live Streaming</li></ul></div>
<div class="foot-col" style="left:817px"><h3>HELPFUL LINKS</h3>
  <div class="address">
    <svg width="11" height="16" viewBox="0 0 11 16" style="margin-top:3px;flex:none"><path d="M5.5 0A5.5 5.5 0 0 0 0 5.5C0 10 5.5 16 5.5 16S11 10 11 5.5A5.5 5.5 0 0 0 5.5 0zm0 8A2.5 2.5 0 1 1 5.5 3a2.5 2.5 0 0 1 0 5z" fill="#fff"/></svg>
    <span>24 Harbor Lane<br>Suite 1, Lakeview<br>United States</span>
  </div>
</div>

<div class="contact-bar">
  <div class="contact-item" style="left:25px"><span class="icon"><svg width="18" height="18" viewBox="0 0 24 24"><path d="M6.6 10.8a15 15 0 0 0 6.6 6.6l2.2-2.2c.3-.3.7-.4 1-.2 1.1.4 2.3.6 3.6.6.6 0 1 .4 1 1V20c0 .6-.4 1-1 1A17 17 0 0 1 3 4c0-.6.4-1 1-1h3.5c.6 0 1 .4 1 1 0 1.3.2 2.5.6 3.6.1.3 0 .7-.2 1z" fill="#fff"/></svg></span>1 800 555 0142</div>
  <span class="divider" style="left:254px"></span>
  <div class="contact-item" style="left:313px"><span class="icon"><svg width="18" height="18" viewBox="0 0 24 24" fill="none" stroke="#fff" stroke-width="2"><rect x="3" y="9" width="18" height="11" rx="1"/><path d="M7 9V3h10v6M7 14h2M11 14h2M15 14h2M7 17h10"/></svg></span>1 800 555 0199</div>
  <span class="divider" style="left:538px"></span>
  <div class="contact-item" style="left:592px"><span class="icon"><svg width="18" height="14" viewBox="0 0 18 14" fill="none" stroke="#fff" stroke-width="1.6"><rect x="1" y="1" width="16" height="12" rx="1"/><path d="M1 2l8 6 8-6"/></svg></span>hello@safeplayindex.com</div>
</div>
<p class="copyright">© 2021 SafePlay Index. All Rights Reserved</p>

</body>
</html>
```